NZ First of it's kind solutions directory and marketplace for busy Mums needs a business card design

We need a business card design for our new nationwide business in NZ (long term plans to go global). We provide solutions to the everyday challenges that busy Mums face by connecting them with quality communities and suppliers of carefully selected, relevant products and services. We sell direct via our online marketplace. The final design should communicate our values of inclusivity, quality and smart solutions. Colours should incorporate our logo colour palette of #477077 and #6ba8b2. Our website is at https://www.brightnestmums.example

Target Market(s)

busy Mums, Age 28 – 50, female, income over $100K, location main centres NZ primarily but NZ wide. Is likely juggling work or career with a young family. Probably had hobbies which have fallen by the wayside.
-Wants to succeed in her chosen career without compromising on family life
-to successfully juggle her career without feeling like she is compromising her children
- Is time poor, something always has to give and it’s generally her health (she’ll stay up late, get stressed)
- probably ex corporate or professional career. Has discretional income

Industry/Entity Type

Business

Contact Information for Business Card

Lena Forbisher, Founder, BrightNestMums.example (Strapline Tap; Gather; Sorted), 47 Kowhai Terrace, Ellerslie, Auckland 1051, New Zealand. Mob: 021 483 517 Ph: +64 (0)9 571 4860

Font styles to use
Other font styles liked:
• Raleway, and/or Architects Daughter

Colors
00a990
33b8a4
86cfc6
cfeae6

Requirements
Must have
• the above details, streamline. the logo and colours associated with those logos
Should not have
• foil or metallic colours

```html
<!DOCTYPE html>
<html lang="en">
<head>
<meta charset="utf-8">
<title>BrightNestMums – Business Card</title>
<link href="https://fonts.googleapis.com/css2?family=Raleway:wght@400;500;600&display=swap" rel="stylesheet">
<style>
  :root {
    --teal: #00ab8f;
    --white: #ffffff;
    --brand-dark: #477077;
    --brand-light: #6ba8b2;
    --backdrop: #e9ebea;
  }
  * { margin: 0; padding: 0; box-sizing: border-box; }
  html, body {
    width: 1200px; height: 1000px; overflow: hidden;
    background: var(--backdrop);
    font-family: "Raleway", sans-serif;
  }
  .canvas { position: relative; width: 1200px; height: 1000px; }

  .card {
    position: absolute;
    background: var(--teal);
    border-radius: 40px;
    overflow: hidden;
    box-shadow: 0 4px 10px rgba(0,0,0,0.18);
  }

  /* Front */
  .card--front { left: 150px; top: 100px; width: 628px; height: 358px; }
  .front-panel {
    position: absolute; left: 28px; top: 30px; width: 572px; height: 300px;
    background: var(--white); border-radius: 32px;
    display: flex; align-items: center; justify-content: center; gap: 16px;
  }
  .brand-dot { width: 34px; height: 34px; border-radius: 50%; background: var(--brand-light); }
  .brand-name {
    font-weight: 600; font-size: 46px; letter-spacing: -1px; color: var(--brand-dark);
  }

  /* Back */
  .card--back { left: 370px; top: 545px; width: 638px; height: 365px; }
  .holder { position: absolute; left: 46px; top: 74px; color: var(--white); }
  .holder-name { font-weight: 400; font-size: 28px; }
  .holder-role { font-weight: 400; font-size: 19px; margin-top: 10px; }

  .back-brand {
    position: absolute; left: 360px; top: 84px;
    display: flex; align-items: center; gap: 10px;
  }
  .back-brand .brand-dot { width: 22px; height: 22px; background: var(--white); opacity: 0.85; }
  .back-brand .brand-name { font-size: 28px; color: var(--white); letter-spacing: -0.5px; }

  .address-band { position: absolute; left: 0; top: 174px; width: 638px; height: 32px; }
  .address {
    position: absolute; left: 134px; top: 180px;
    font-size: 16.5px; font-weight: 500; color: var(--teal);
  }

  .contacts { position: absolute; left: 46px; top: 226px; list-style: none; color: var(--white); }
  .contact { display: flex; align-items: center; height: 34px; font-size: 19px; }
  .contact svg { width: 22px; height: 22px; margin-right: 15px; flex: none; }
  .contact--landline span { margin-left: 6px; }
  .strapline { font-size: 13.5px; margin-left: 6px; }
</style>
</head>
<body>
<main class="canvas">

  <section class="card card--front" aria-label="Card front">
    <div class="front-panel">
      <span class="brand-dot"></span>
      <span class="brand-name">BrightNestMums</span>
    </div>
  </section>

  <section class="card card--back" aria-label="Card back">
    <div class="holder">
      <p class="holder-name">Lena Forbisher</p>
      <p class="holder-role">Founder</p>
    </div>

    <div class="back-brand">
      <span class="brand-dot"></span>
      <span class="brand-name">BrightNestMums</span>
    </div>

    <svg class="address-band" viewBox="0 0 638 32" aria-hidden="true">
      <rect x="0" y="0" width="638" height="2" fill="#ffffff"/>
      <path d="M110 3 H638 V29 H122 Q114 29 112 22 Z" fill="#ffffff"/>
    </svg>
    <p class="address">47 Kowhai Terrace, Ellerslie, Auckland 1051, New Zealand</p>

    <ul class="contacts">
      <li class="contact contact--landline">
        <svg viewBox="0 0 24 24" aria-hidden="true">
          <path d="M3 8 Q12 2 21 8 L19 11 L16 10 L16 8 Q12 6.5 8 8 L8 10 L5 11 Z" fill="#fff"/>
          <rect x="5" y="12" width="14" height="9" rx="2" fill="#fff"/>
          <circle cx="12" cy="16.5" r="2.4" fill="#00ab8f"/>
        </svg>
        <span>+64 (0)9 571 4860</span>
      </li>
      <li class="contact">
        <svg viewBox="0 0 24 24" aria-hidden="true">
          <path d="M6.6 10.8a15 15 0 0 0 6.6 6.6l2.2-2.2a1 1 0 0 1 1-.25 11 11 0 0 0 3.6.6 1 1 0 0 1 1 1V20a1 1 0 0 1-1 1A17 17 0 0 1 3 4a1 1 0 0 1 1-1h3.5a1 1 0 0 1 1 1 11 11 0 0 0 .6 3.6 1 1 0 0 1-.25 1z" fill="#fff"/>
        </svg>
        <span>021 483 517</span>
      </li>
      <li class="contact">
        <svg viewBox="0 0 24 24" aria-hidden="true" fill="none" stroke="#fff" stroke-width="2">
          <circle cx="12" cy="12" r="9.5"/>
          <ellipse cx="12" cy="12" rx="4" ry="9.5"/>
          <path d="M2.5 12h19M4 7h16M4 17h16"/>
        </svg>
        <span>www.brightnestmums.example</span>
        <span class="strapline">( Strapline Tap; Gather; Sorted )</span>
      </li>
    </ul>
  </section>

</main>
</body>
</html>
```